Tall Fern Roofing Business Card

Need a business card with the logo that was designed here

Contact Information for Business Card

Name, Title, Phone, Email, Website, Company name

```html
<!DOCTYPE html>
<html lang="en">
<head>
<meta charset="utf-8">
<title>Tall Fern Roofing – Business Card</title>
<link href="https://fonts.googleapis.com/css2?family=Montserrat:wght@400;500;700&display=swap" rel="stylesheet">
<style>
  :root {
    --backdrop: #d3d6d7;
    --paper: #f7f7f5;
    --brand-blue: #1e3f9e;
    --ink: #2f3033;
    --ink-soft: #4a4b4f;
  }
  * { box-sizing: border-box; margin: 0; padding: 0; }
  html, body {
    width: 1200px; height: 829px; overflow: hidden;
    background: var(--backdrop);
    font-family: "Montserrat", Arial, sans-serif;
  }
  .stage {
    width: 1200px; height: 829px;
    display: flex; align-items: center; justify-content: center; gap: 40px;
  }
  .card {
    position: relative;
    width: 540px; height: 314px;
    background: var(--paper);
    border-bottom: 4px solid var(--brand-blue);
    box-shadow: 0 10px 24px rgba(0,0,0,0.12);
  }
  .wordmark {
    display: flex; align-items: center; gap: 10px;
    color: var(--brand-blue); font-weight: 700; letter-spacing: 0.04em;
    text-transform: uppercase; white-space: nowrap;
  }
  .wordmark__square { background: var(--brand-blue); flex: none; }

  /* Info side */
  .card--info .person { position: absolute; left: 36px; top: 40px; }
  .person__name { font-size: 21px; font-weight: 700; letter-spacing: 0.04em; color: var(--ink); }
  .person__first { color: var(--brand-blue); }
  .person__title { font-size: 13px; color: var(--ink-soft); margin-top: 2px; }
  .card--info .divider {
    position: absolute; left: 36px; right: 30px; top: 104px;
    height: 1px; background: var(--brand-blue);
  }
  .card--info .wordmark {
    position: absolute; right: 30px; top: 50px; font-size: 16px;
  }
  .card--info .wordmark__square { width: 12px; height: 12px; }
  .contacts { position: absolute; left: 36px; top: 122px; list-style: none; }
  .contacts li {
    display: flex; align-items: center; gap: 9px;
    font-size: 13.5px; color: var(--ink); line-height: 25px;
  }
  .contacts svg { width: 11px; height: 11px; fill: var(--brand-blue); flex: none; }
  .address {
    position: absolute; right: 30px; bottom: 30px;
    text-align: right; font-size: 14px; color: var(--ink); line-height: 21px;
  }

  /* Brand side */
  .card--brand { display: flex; align-items: center; justify-content: center; }
  .card--brand .wordmark { font-size: 32px; gap: 14px; }
  .card--brand .wordmark__square { width: 22px; height: 22px; }
</style>
</head>
<body>
<main class="stage">
  <section class="card card--info">
    <div class="person">
      <h1 class="person__name"><span class="person__first">DECLAN</span> MORROW</h1>
      <p class="person__title">Managing Director</p>
    </div>
    <div class="wordmark"><span class="wordmark__square"></span>Tall Fern Roofing</div>
    <div class="divider"></div>
    <ul class="contacts">
      <li>
        <svg viewBox="0 0 24 24" aria-hidden="true"><path d="M6.6 10.8a15.1 15.1 0 0 0 6.6 6.6l2.2-2.2a1 1 0 0 1 1-.25 11.4 11.4 0 0 0 3.6.57 1 1 0 0 1 1 1V20a1 1 0 0 1-1 1A17 17 0 0 1 3 4a1 1 0 0 1 1-1h3.5a1 1 0 0 1 1 1c0 1.25.2 2.45.57 3.57a1 1 0 0 1-.25 1z"/></svg>
        0491 555 017
      </li>
      <li>
        <svg viewBox="0 0 24 24" aria-hidden="true"><path d="M2 5h20v14H2zm2 2v.5l8 5 8-5V7zm0 2.8V17h16V9.8l-8 5z"/></svg>
        info@tallfernroofing.com
      </li>
      <li>
        <svg viewBox="0 0 24 24" aria-hidden="true"><path d="M12 2a10 10 0 1 0 0 20 10 10 0 0 0 0-20zm6.9 9h-3a15 15 0 0 0-1.3-5.6A8 8 0 0 1 18.9 11zM12 4.1c.9 1.2 1.8 3.5 1.9 6.9h-3.8c.1-3.4 1-5.7 1.9-6.9zM9.4 5.4A15 15 0 0 0 8.1 11h-3a8 8 0 0 1 4.3-5.6zM5.1 13h3a15 15 0 0 0 1.3 5.6A8 8 0 0 1 5.1 13zm6.9 6.9c-.9-1.2-1.8-3.5-1.9-6.9h3.8c-.1 3.4-1 5.7-1.9 6.9zm2.6-1.3a15 15 0 0 0 1.3-5.6h3a8 8 0 0 1-4.3 5.6z"/></svg>
        www.tallfernroofing.com
      </li>
    </ul>
    <address class="address">
      1480 W Harlow Street<br>
      Marden County Name 5240
    </address>
  </section>

  <section class="card card--brand">
    <div class="wordmark"><span class="wordmark__square"></span>Tall Fern Roofing</div>
  </section>
</main>
</body>
</html>
```